A5 Patient Information Booklet (Chiropractic Clinic) 4-8 pages

Here’s a polished, professional rewrite of your full brief and content, with clearer structure, corrected language, and a premium tone:

---

**Project Title:** Premium Patient Information Brochure (Chiropractic & Wellness Clinic)

---

### **Overview**

We are a health and wellness clinic seeking a premium, high-end patient information brochure to provide following a patient’s initial consultation and first treatment.

The purpose of this booklet is to:

* Reinforce trust and professionalism
* Help patients understand what to expect next
* Encourage adherence to care recommendations
* Position the clinic as calm, expert-led, and results-driven

---

### **Format**

* 4–8 page booklet (A5 or similar size)
* Print-ready and digital versions required

---

### **Target Audience**

Patients who have just completed their initial consultation and may have begun treatment. They may already be experiencing physical or mental changes, so the brochure should guide, reassure, and educate them on what comes next.

---

### **Tone & Style**

* Premium, calm, and reassuring
* Modern wellness aesthetic (not overly clinical)
* Clean layout with minimal clutter
* Soft, neutral colour palette (whites, creams, muted greens, soft blues)
* Elegant typography (e.g. Montserrat / Lato)
* High-end, trustworthy, and professional feel

---

### **Key Messages**

#### 1. Listen to Your Body

Patients may feel different after treatment. Reassure them that this is normal and part of the healing process.

#### 2. Post-Treatment Advice

* Stay well hydrated
* Rest if needed
* Avoid overexertion if the body requires recovery

#### 3. Healing is a Journey (Core Concept)

A strong visual metaphor of a **“road to recovery”** or **journey** should be central to the design.

This journey should clearly illustrate three phases:

* **Phase 1: Initial Care (Weeks 1–6)**
Focus: Reducing pain/discomfort, calming the body, and initiating response to treatment

* **Phase 2: Corrective Care (Weeks 6–12)**
Focus: Addressing underlying issues, improving function, and creating lasting change

* **Phase 3: Wellness / Maintenance (Ongoing)**
Focus: Maintaining progress, preventing relapse, and supporting long-term wellbeing

**Important:**

* Emphasise that this is not a quick fix
* Progress requires time and consistency
* Each patient follows an individualised care plan
* The journey should feel structured, positive, and achievable

#### 4. Personalised Care

Reinforce that every treatment plan is tailored specifically to the individual.

#### 5. Professional Reassurance

Patients should feel confident they are in expert hands and supported throughout their journey.

---

### **Design Direction**

* Use imagery that reflects calmness, progression, and wellness (e.g. pathways, nature, soft gradients)
* Avoid generic stock imagery
* **Only use original clinic images from website and social media**
* Prioritise white space and clarity
* Aim for a luxury spa/medical hybrid aesthetic

---

## **Content Structure (Page-by-Page)**

### **Front Cover**

* Clean, minimal, premium design
* Clinic branding

---

### **Page 1: Patient Case Summary**

**Title:** *Welcome to Fernwell Spine Studio*

Thank you for choosing Fernwell Spine Studio.

This booklet is designed to guide you through:

* What we found during your initial consultation
* Your personalised recommended treatment plan
* Your road to recovery
* Long-term wellness care
* Why we take the approach we do

---

### **Page 2: Your Care Journey**

**Stage 1: Your Initial Consultation**

Today we completed a comprehensive assessment of your health and function, including:

* Full case history and discussion of your symptoms and goals
* Orthopaedic and neurological testing
* Postural and movement assessment
* Initial treatment (where appropriate)

**What this tells us:**

* How your body is currently functioning
* Where areas of stress or dysfunction may be present
* The most appropriate and effective path forward for your care

---

### **Page 3: Your Suggested Treatment Plan**

Based on today’s findings, your recommended care plan is:

**______ treatments over ______ weeks**

This should be viewed alongside your *Road to Recovery* to help you understand what to expect.

We have also discussed:

* Expected timelines for improvement
* Available payment options

**After Treatment:**
It is common to feel different following treatment. This is a normal response as your body begins to adapt and respond.

We recommend:

* Staying well hydrated
* Allowing time for rest and recovery
* Avoiding overexertion if your body feels it needs it

---

### **Page 4: What to Expect Next**

Healing is not always linear—it is a process that occurs over time.

Your care will typically progress through the following stages:

* **Relief Care**
Focused on reducing discomfort and calming the body

* **Corrective Care**
Focused on addressing underlying issues and improving function
(This phase may include prescribed exercises)

* **Maintenance / Wellness Care**
Focused on sustaining progress, preventing recurrence, and supporting long-term health

---

### **Page 5: Understanding Chiropractic Care**

**What is Chiropractic?**
Chiropractic care focuses on the relationship between the spine, nervous system, and overall body function.

By improving spinal movement and alignment, chiropractic care helps support the nervous system, allowing the body to function and heal more effectively.

**About Fernwell Spine Studio**
At Fernwell Spine Studio, our approach is centred around personalised, patient-focused care. We aim to not only relieve symptoms but to address underlying causes and support long-term wellbeing.

---

### **Back Page**

* Clinic contact details
* Website
* Social media icons/handles

**Closing Message:**
“A healthier, stronger you—supported every step of the way.”

---

### **Deliverables**

* Print-ready PDF
* Editable source files

---

### **Additional Notes**

* The brochure should feel valuable and worth keeping
* Encourage long-term care in a subtle, non-pushy way
* Maintain clarity, readability, and strong visual hierarchy
* Balance professionalism with warmth and approachability

---

If you’d like, I can also turn this into **actual brochure copy (fully written, patient-facing text)** or help you refine it further for a designer.

Existing patients who want to feel better and look after themselves that is given after their initil consultation appointment

Chiropractic, wellness, health

• Montserrat or Lato

0094D4
00A9DD
6FCCEA
C7EBF8
E9F6FB
00AB8E
00BBA5
67D7C9
C6EFE9
E9F9F6
6B429C
8869AF
B7A5CE
E3DAEB
F3F0F8

• my own photos, look premium wellness, be clear and simple to understand for patients journey or what to expect next and over time
• USe my social media/website for ideas
• generic photos and images

```html
<!DOCTYPE html>
<html lang="en">
<head>
<meta charset="utf-8">
<title>Fernwell Spine Studio – Patient Booklet</title>
<link rel="stylesheet" href="https://fonts.googleapis.com/css2?family=Montserrat:wght@400;500;600&family=Lato:wght@400;700&family=Cormorant+Garamond:wght@500;600&family=Dancing+Script:wght@500&display=swap">
<style>
:root{
  --teal:#16978b;
  --teal-mid:#3fb5a7;
  --teal-soft:#c6efe9;
  --teal-pale:#e9f6f4;
  --purple:#6b429c;
  --purple-mid:#8869af;
  --purple-soft:#b7a5ce;
  --purple-pale:#f3f0f8;
  --ink:#2f3d4c;
  --body:#3c4650;
  --line:#c9d3d6;
  --stage:#ececec;
  --paper:#fbfbfb;
}
*{box-sizing:border-box;margin:0;padding:0}
html,body{width:1200px;height:800px;overflow:hidden;background:var(--stage)}
body{position:relative;font-family:"Lato",sans-serif;color:var(--body)}
.page{position:absolute;width:581px;height:384px;background:var(--paper);overflow:hidden;box-shadow:0 2px 6px rgba(0,0,0,.12)}
.page--cover{left:9px;top:9px;background:linear-gradient(135deg,#ece6f4 0%,#f7f8f8 45%,#eef6f5 100%)}
.page--expect{left:607px;top:9px}
.page--journey{left:9px;top:406px}
.page--plan{left:607px;top:406px}
.abs{position:absolute}
.center{left:0;right:0;text-align:center}
.waves{position:absolute;inset:0;width:100%;height:100%}
.heading{font-family:"Montserrat",sans-serif;letter-spacing:.08em;line-height:1}
.rule{position:absolute;height:2px;width:28px;background:var(--teal);left:50%;margin-left:-14px}
.brand-ring{position:absolute;border-radius:50%;border:3px solid var(--teal);border-left-color:var(--purple-mid);border-top-color:var(--purple-mid)}
.brand-name{font-family:"Cormorant Garamond",serif;font-weight:600;color:var(--ink);letter-spacing:.05em;line-height:1}
.brand-sub{font-family:"Montserrat",sans-serif;color:var(--teal);letter-spacing:.15em;line-height:1}
.script{font-family:"Dancing Script",cursive;color:var(--teal);line-height:1.3}
.page-no{position:absolute;font-family:"Montserrat",sans-serif;font-size:13px;color:#fff;line-height:1}
.small{font-size:10px;line-height:1.5}

/* cover */
.cover-title-1{top:210px;font-size:20px;color:var(--teal);font-weight:500}
.cover-title-2{top:237px;font-size:28px;color:var(--ink);font-weight:600}
.cover-intro{top:290px;font-size:11px;line-height:1.45;color:var(--ink)}
.leaf-art{left:470px;top:190px;width:105px;height:180px;border-radius:50% 50% 40% 40%;background:radial-gradient(ellipse at center,rgba(183,165,206,.35),rgba(183,165,206,0) 70%)}

/* expect */
.expect-title{top:24px;font-size:25px;font-weight:600}
.expect-title .t{color:var(--teal)} .expect-title .p{color:var(--purple)}
.expect-sub{top:56px;font-size:12px;letter-spacing:.2em;color:var(--ink)}
.expect-intro{top:94px;color:var(--ink)}
.tip{position:absolute;top:138px;width:150px;text-align:center}
.tip-icon{width:74px;height:74px;border-radius:50%;margin:0 auto;display:flex;align-items:center;justify-content:center}
.tip-icon--teal{background:var(--teal-pale)}
.tip-icon--purple{background:#ece6f4}
.tip-title{font-family:"Montserrat",sans-serif;font-weight:500;font-size:12px;letter-spacing:.03em;margin-top:14px;line-height:1}
.tip-text{margin-top:10px;font-size:9.5px;line-height:1.55;color:var(--body)}
.col-divider{position:absolute;top:145px;width:1px;height:152px;background:var(--line)}
.note{left:61px;top:320px;width:381px;height:47px;border-radius:10px;background:var(--teal-pale);display:flex;align-items:center;gap:16px;padding-left:18px}
.note p{font-size:9.5px;line-height:1.55;color:var(--ink)}

/* journey */
.journey-title{top:20px;font-size:22px;font-weight:600}
.journey-title .t{color:var(--teal)} .journey-title .p{color:var(--purple)}
.journey-intro{top:47px;font-size:10.5px;line-height:1.45;color:var(--ink)}
.phase{position:absolute;top:164px;width:170px;text-align:center;font-family:"Montserrat",sans-serif;line-height:1}
.phase h3{font-size:12px;font-weight:500;letter-spacing:.04em}
.phase .name{font-size:10px;letter-spacing:.06em;margin-top:6px}
.phase .weeks{font-size:8.5px;letter-spacing:.06em;margin-top:5px}
.phase--teal{color:var(--teal)} .phase--mid{color:#2e8fa0} .phase--purple{color:var(--purple)}
.bullets{position:absolute;top:214px;list-style:none;font-size:8.5px;color:var(--ink);line-height:1}
.bullets li{margin-bottom:8.5px;padding-left:11px;position:relative}
.bullets li::before{content:"";position:absolute;left:0;top:2px;width:3.5px;height:3.5px;border-radius:50%;background:var(--teal)}
.bullets--purple li::before{background:var(--purple)}
.timeline{left:48px;top:284px;width:479px;height:48px;border:1px solid var(--line);border-radius:8px}
.tl-label{position:absolute;font-family:"Montserrat",sans-serif;font-size:10px;letter-spacing:.06em;text-align:center;line-height:1.4}
.journey-script{top:341px;font-size:14px}

/* plan */
.plan-left{left:0;top:0;width:264px;height:384px}
.plan-title{top:31px;font-size:14px;color:var(--teal);font-weight:500;letter-spacing:.06em}
.field-label{position:absolute;left:24px;font-size:9.5px;color:var(--ink);line-height:1}
.field-line{position:absolute;height:0;border-bottom:1px dotted #9aa4a8}
.plan-box{left:21px;top:219px;width:220px;height:117px;border-radius:14px;background:var(--teal-pale)}
.plan-box p{position:absolute;left:63px;width:145px;font-size:9px;line-height:1.6;color:var(--ink)}
.plan-right{left:264px;top:0;width:317px;height:384px;background:linear-gradient(160deg,#e3daeb 0%,#efe9f5 55%,#ece6f3 100%);box-shadow:inset 8px 0 10px -8px rgba(0,0,0,.15)}
.contact{position:absolute;left:59px;font-size:9.5px;color:var(--ink);line-height:1.45}
.contact-icon{position:absolute;left:52px}
.follow{top:270px;font-family:"Montserrat",sans-serif;font-size:10px;color:var(--teal);letter-spacing:.08em;font-weight:500}
.social-dot{position:absolute;top:307px;width:20px;height:20px;border-radius:50%;background:var(--teal)}
.handle{top:338px;font-size:9px;color:var(--ink)}
</style>
</head>
<body>

<!-- Front cover -->
<section class="page page--cover">
  <svg class="waves" viewBox="0 0 581 384" preserveAspectRatio="none" aria-hidden="true">
    <defs>
      <linearGradient id="coverTeal" x1="0" y1="0" x2="1" y2="0">
        <stop offset="0" stop-color="#2aa296"/><stop offset=".6" stop-color="#8fd3c9"/><stop offset="1" stop-color="#e4f3f1"/>
      </linearGradient>
    </defs>
    <path d="M0 230 C120 300 260 360 420 380 L0 384 Z" fill="url(#coverTeal)" opacity=".9"/>
    <path d="M0 255 C140 320 300 375 581 370 L581 384 L0 384 Z" fill="#dfeeee" opacity=".6"/>
    <path d="M0 160 C90 250 230 330 581 330" fill="none" stroke="#fff" stroke-width="1.2" opacity=".8"/>
    <path d="M0 290 C180 350 360 378 581 360" fill="none" stroke="#fff" stroke-width="1" opacity=".7"/>
    <path d="M581 150 C480 210 420 260 380 384" fill="none" stroke="#fff" stroke-width="1" opacity=".7"/>
  </svg>
  <div class="brand-ring" style="left:246px;top:49px;width:86px;height:86px"></div>
  <div class="abs center brand-name" style="top:145px;font-size:20px">FERNWELL SPINE STUDIO</div>
  <div class="abs center brand-sub" style="top:169px;font-size:9.5px">CHIROPRACTIC &amp; WELLNESS</div>
  <div class="rule" style="top:192px"></div>
  <h1 class="abs center heading cover-title-1">YOUR PATH TO</h1>
  <div class="abs center heading cover-title-2">BETTER HEALTH</div>
  <div class="rule" style="top:276px;background:var(--ink)"></div>
  <p class="abs center cover-intro">Your personalised guide<br>to recovery and long-term wellness</p>
  <div class="abs leaf-art" role="img" aria-label="Faint botanical leaf sprig illustration"></div>
</section>

<!-- What to expect -->
<section class="page page--expect">
  <svg class="waves" viewBox="0 0 581 384" preserveAspectRatio="none" aria-hidden="true">
    <path d="M480 0 C530 10 565 25 581 45 L581 0 Z" fill="#9fd8d0" opacity=".8"/>
    <path d="M430 0 C500 20 550 50 581 90" fill="none" stroke="var(--purple-soft)" stroke-width="1"/>
    <path d="M581 320 C540 320 505 350 480 384 L581 384 Z" fill="url(#expTeal)"/>
    <defs><linearGradient id="expTeal" x1="0" y1="0" x2="1" y2="1"><stop offset="0" stop-color="#6fcfc2"/><stop offset="1" stop-color="#1f9a8d"/></linearGradient></defs>
  </svg>
  <h2 class="abs center heading expect-title"><span class="t">WHAT TO</span> <span class="p">EXPECT</span></h2>
  <div class="abs center heading expect-sub">AFTER YOUR TREATMENT</div>
  <div class="rule" style="top:81px"></div>
  <p class="abs center expect-intro small">Your body is beginning to respond and heal.<br>Here's how you can support that process:</p>

  <div class="tip" style="left:30px">
    <div class="tip-icon tip-icon--teal">
      <svg width="34" height="44" viewBox="0 0 34 44" aria-hidden="true"><path d="M17 3 C10 15 4 22 4 29 a13 13 0 0 0 26 0 C30 22 24 15 17 3 Z" fill="none" stroke="var(--teal)" stroke-width="2"/><path d="M10 30 a7 7 0 0 0 7 7" fill="none" stroke="var(--teal)" stroke-width="2"/></svg>
    </div>
    <div class="tip-title" style="color:var(--teal)">STAY HYDRATED</div>
    <p class="tip-text">Drink plenty of water to<br>support your body's natural<br>healing response.</p>
  </div>
  <div class="col-divider" style="left:182px"></div>
  <div class="tip" style="left:183px">
    <div class="tip-icon tip-icon--teal">
      <svg width="46" height="34" viewBox="0 0 46 34" aria-hidden="true"><path d="M4 4 Q23 9 42 4 Q38 17 42 30 Q23 25 4 30 Q8 17 4 4 Z" fill="none" stroke="var(--teal)" stroke-width="2"/><text x="13" y="22" font-family="Montserrat,sans-serif" font-size="9" fill="var(--teal)">z</text><text x="19" y="19" font-family="Montserrat,sans-serif" font-size="10" fill="var(--teal)">z</text><text x="26" y="16" font-family="Montserrat,sans-serif" font-size="11" fill="var(--teal)">z</text></svg>
    </div>
    <div class="tip-title" style="color:var(--teal)">REST &amp; RECOVER</div>
    <p class="tip-text">Allow your body time<br>to adjust and respond<br>to treatment.</p>
  </div>
  <div class="col-divider" style="left:336px"></div>
  <div class="tip" style="left:340px">
    <div class="tip-icon tip-icon--purple">
      <svg width="30" height="46" viewBox="0 0 30 46" aria-hidden="true"><circle cx="15" cy="7" r="5" fill="none" stroke="var(--purple)" stroke-width="2"/><path d="M8 44 V28 H5 V17 a4 4 0 0 1 4-4 H21 a4 4 0 0 1 4 4 V28 H22 V44 M15 30 V44" fill="none" stroke="var(--purple)" stroke-width="2" stroke-linejoin="round"/><path d="M15 25 l-4-4 a2.3 2.3 0 0 1 4-2.5 a2.3 2.3 0 0 1 4 2.5 Z" fill="var(--purple)"/></svg>
    </div>
    <div class="tip-title" style="color:var(--purple)">LISTEN TO YOUR BODY</div>
    <p class="tip-text">You may feel different—<br>this is normal and part of<br>the healing process.</p>
  </div>

  <div class="abs note">
    <svg width="28" height="26" viewBox="0 0 28 26" aria-hidden="true"><path d="M14 24 L3 13 a6.5 6.5 0 0 1 11-8 a6.5 6.5 0 0 1 11 8 Z" fill="none" stroke="var(--teal)" stroke-width="1.8" stroke-linejoin="round"/></svg>
    <p>Everyone's experience is unique. If you have any concerns,<br>please reach out — we are here for you.</p>
  </div>
  <div class="page-no" style="left:548px;top:361px">01</div>
</section>

<!-- Recovery journey -->
<section class="page page--journey">
  <svg class="waves" viewBox="0 0 581 384" preserveAspectRatio="none" aria-hidden="true">
    <defs>
      <linearGradient id="road" x1="0" y1="0" x2="1" y2="0">
        <stop offset="0" stop-color="#3fb3a5"/><stop offset=".45" stop-color="#5aa9b0"/><stop offset=".75" stop-color="#7f62ad"/><stop offset="1" stop-color="#c9bbde" stop-opacity=".4"/>
      </linearGradient>
      <linearGradient id="jPurple" x1="0" y1="0" x2="1" y2="1"><stop offset="0" stop-color="#d9cdea"/><stop offset="1" stop-color="#9a80c0"/></linearGradient>
    </defs>
    <path d="M-10 212 C40 150 70 140 140 138 C200 136 220 96 290 96 C330 96 330 150 375 152 C420 154 430 110 475 112 C520 114 545 140 590 160" fill="none" stroke="url(#road)" stroke-width="22" stroke-linecap="round"/>
    <path d="M-10 212 C40 150 70 140 140 138 C200 136 220 96 290 96 C330 96 330 150 375 152 C420 154 430 110 475 112 C520 114 545 140 590 160" fill="none" stroke="#fff" stroke-width="1.4" stroke-dasharray="6 5"/>
    <path d="M581 320 C540 322 505 350 490 384 L581 384 Z" fill="url(#jPurple)"/>
    <line x1="105" y1="137" x2="105" y2="150" stroke="var(--teal)" stroke-width="1" stroke-dasharray="2 2"/>
    <line x1="290" y1="125" x2="290" y2="150" stroke="#2e8fa0" stroke-width="1" stroke-dasharray="2 2"/>
    <line x1="463" y1="120" x2="463" y2="150" stroke="var(--purple)" stroke-width="1" stroke-dasharray="2 2"/>
    <circle cx="105" cy="153" r="2" fill="var(--teal)"/><circle cx="290" cy="153" r="2" fill="#2e8fa0"/><circle cx="463" cy="153" r="2" fill="var(--purple)"/>
    <g font-family="Montserrat,sans-serif" font-weight="600" text-anchor="middle" fill="#fff">
      <path d="M105 137 L95 124 A20 20 0 1 1 115 124 Z" fill="var(--teal)" stroke="#fff" stroke-width="2"/>
      <text x="105" y="117" font-size="20">1</text>
      <path d="M290 125 L280 112 A20 20 0 1 1 300 112 Z" fill="#1e8e98" stroke="#fff" stroke-width="2"/>
      <text x="290" y="105" font-size="20">2</text>
      <path d="M463 120 L453 107 A20 20 0 1 1 473 107 Z" fill="var(--purple)" stroke="#fff" stroke-width="2"/>
      <text x="463" y="100" font-size="20">3</text>
    </g>
  </svg>
  <h2 class="abs center heading journey-title"><span class="t">YOUR RECOVERY</span> <span class="p">JOURNEY</span></h2>
  <p class="abs center journey-intro">Healing is a journey, not a quick fix.<br>With the right care and consistency, lasting change is possible.</p>

  <div class="phase phase--teal" style="left:20px"><h3>PHASE 1</h3><div class="name">INITIAL CARE</div><div class="weeks">(WEEKS 1–6)</div></div>
  <div class="phase phase--mid" style="left:205px"><h3>PHASE 2</h3><div class="name">CORRECTIVE CARE</div><div class="weeks">(WEEKS 6–12)</div></div>
  <div class="phase phase--purple" style="left:378px"><h3>PHASE 3</h3><div class="name">WELLNESS CARE</div><div class="weeks">(ONGOING)</div></div>

  <ul class="bullets" style="left:48px"><li>Reduce pain &amp; discomfort</li><li>Calm your body</li><li>Begin healing response</li></ul>
  <ul class="bullets" style="left:226px"><li>Address underlying issues</li><li>Improve movement &amp; function</li><li>Build stability</li></ul>
  <ul class="bullets bullets--purple" style="left:403px"><li>Maintain progress</li><li>Prevent future issues</li><li>Support long-term wellbeing</li></ul>

  <div class="abs timeline">
    <svg class="abs" style="left:24px;top:12px" width="22" height="22" viewBox="0 0 22 22" aria-hidden="true"><rect x="2" y="4" width="18" height="16" rx="2" fill="none" stroke="var(--teal)" stroke-width="1.6"/><line x1="2" y1="9" x2="20" y2="9" stroke="var(--teal)" stroke-width="1.6"/><line x1="7" y1="1.5" x2="7" y2="6" stroke="var(--teal)" stroke-width="1.6"/><line x1="15" y1="1.5" x2="15" y2="6" stroke="var(--teal)" stroke-width="1.6"/><g fill="var(--teal)"><rect x="5" y="11.5" width="2" height="2"/><rect x="10" y="11.5" width="2" height="2"/><rect x="15" y="11.5" width="2" height="2"/><rect x="5" y="15.5" width="2" height="2"/><rect x="10" y="15.5" width="2" height="2"/><rect x="15" y="15.5" width="2" height="2"/></g></svg>
    <div class="tl-label" style="left:58px;top:10px;color:var(--teal)">WEEKS<br>1–6</div>
    <svg class="abs" style="left:110px;top:22px" width="54" height="6" viewBox="0 0 54 6" aria-hidden="true"><line x1="0" y1="3" x2="52" y2="3" stroke="var(--teal)" stroke-width="1"/><path d="M48 0 L53 3 L48 6" fill="none" stroke="var(--teal)" stroke-width="1"/></svg>
    <svg class="abs" style="left:180px;top:11px" width="24" height="24" viewBox="0 0 24 24" aria-hidden="true"><circle cx="12" cy="12" r="10" fill="none" stroke="#2e8fa0" stroke-width="1.6"/><path d="M12 6 V12 L16 15" fill="none" stroke="#2e8fa0" stroke-width="1.6"/></svg>
    <div class="tl-label" style="left:226px;top:10px;color:#2e8fa0">MONTHS<br>6–12</div>
    <svg class="abs" style="left:280px;top:22px" width="54" height="6" viewBox="0 0 54 6" aria-hidden="true"><line x1="0" y1="3" x2="52" y2="3" stroke="var(--purple)" stroke-width="1"/><path d="M48 0 L53 3 L48 6" fill="none" stroke="var(--purple)" stroke-width="1"/></svg>
    <svg class="abs" style="left:348px;top:12px" width="26" height="22" viewBox="0 0 26 22" aria-hidden="true"><path d="M13 20 L3 10.5 a5.8 5.8 0 0 1 10-7 a5.8 5.8 0 0 1 10 7 Z" fill="none" stroke="var(--purple)" stroke-width="1.8" stroke-linejoin="round"/></svg>
    <div class="tl-label" style="left:384px;top:10px;color:var(--purple)">LONG-TERM<br>WELLNESS</div>
  </div>
  <p class="abs center script journey-script">Every journey is unique and your care plan is tailored specifically to you.</p>
  <div class="page-no" style="left:550px;top:361px">02</div>
</section>

<!-- Personalised plan + back cover -->
<section class="page page--plan">
  <div class="abs plan-left">
    <div class="abs center heading plan-title">YOUR PERSONALISED PLAN</div>
    <div class="rule" style="top:57px"></div>
    <div class="field-label" style="top:83px">Patient Name:</div>
    <div class="field-line" style="left:24px;top:117px;width:218px"></div>
    <div class="field-label" style="top:146px">Your Suggested Care Plan:</div>
    <div class="field-line" style="left:24px;top:184px;width:54px"></div>
    <div class="field-label" style="left:84px;top:176px">treatments over</div>
    <div class="field-line" style="left:157px;top:184px;width:52px"></div>
    <div class="field-label" style="left:212px;top:176px">weeks</div>
    <div class="abs plan-box">
      <svg class="abs" style="left:8px;top:19px" width="46" height="46" viewBox="0 0 46 46" aria-hidden="true"><circle cx="23" cy="23" r="21" fill="none" stroke="var(--teal)" stroke-width="1.5"/><path d="M23 33 L13.5 23.5 a5.5 5.5 0 0 1 9.5-6.5 a5.5 5.5 0 0 1 9.5 6.5 Z" fill="none" stroke="var(--teal)" stroke-width="1.8" stroke-linejoin="round"/></svg>
      <p style="top:20px">Your plan is tailored specifically<br>to your body and goals.</p>
      <div class="abs" style="left:63px;top:62px;width:140px;height:1px;background:#cfe3e0"></div>
      <p style="top:74px">We will review your progress<br>together along the way.</p>
      <div class="abs" role="img" aria-label="Faint leaf sprig illustration" style="left:170px;top:62px;width:60px;height:62px;background:radial-gradient(ellipse at center,rgba(103,215,201,.3),rgba(103,215,201,0) 70%)"></div>
    </div>
  </div>

  <div class="abs plan-right">
    <svg class="waves" viewBox="0 0 317 384" preserveAspectRatio="none" aria-hidden="true">
      <defs><linearGradient id="backTeal" x1="0" y1="0" x2="1" y2="1"><stop offset="0" stop-color="#7fd3c7"/><stop offset="1" stop-color="#1f9a8d"/></linearGradient></defs>
      <path d="M140 0 C200 60 230 200 317 260" fill="none" stroke="#fff" stroke-width="1" opacity=".7"/>
      <path d="M317 300 C270 310 240 345 225 384 L317 384 Z" fill="url(#backTeal)"/>
    </svg>
    <div class="brand-ring" style="left:112px;top:24px;width:58px;height:58px"></div>
    <div class="abs center brand-name" style="top:85px;font-size:16px">FERNWELL SPINE STUDIO</div>
    <div class="abs center brand-sub" style="top:104px;font-size:8px">CHIROPRACTIC &amp; WELLNESS</div>
    <p class="abs center script" style="top:124px;font-size:16px">We're here to support you<br>every step of your journey.</p>

    <svg class="contact-icon" style="left:49px;top:183px" width="14" height="18" viewBox="0 0 14 18" aria-hidden="true"><path d="M7 17 C3 11 1 8.5 1 6 a6 6 0 0 1 12 0 C13 8.5 11 11 7 17 Z" fill="var(--teal)"/><circle cx="7" cy="6" r="2.2" fill="#efe9f5"/></svg>
    <p class="contact" style="left:79px;top:182px">4/12 Harbour Lane,<br>Riverton TAS 7300</p>
    <svg class="contact-icon" style="left:48px;top:218px" width="16" height="16" viewBox="0 0 16 16" aria-hidden="true"><circle cx="8" cy="8" r="7" fill="none" stroke="var(--teal)" stroke-width="1.4"/><path d="M5.3 4.6 l1.4-.3 .8 1.8-1 .8 a5 5 0 0 0 2.3 2.3 l.8-1 1.8.8-.3 1.4 c-3 .4-6.2-2.8-5.8-5.8 Z" fill="var(--teal)"/></svg>
    <p class="contact" style="left:79px;top:219px">(03) 6400 2718</p>
    <svg class="contact-icon" style="left:48px;top:240px" width="16" height="16" viewBox="0 0 16 16" aria-hidden="true"><g fill="none" stroke="var(--teal)" stroke-width="1.2"><circle cx="8" cy="8" r="7"/><ellipse cx="8" cy="8" rx="3" ry="7"/><line x1="1" y1="8" x2="15" y2="8"/><path d="M2.5 4.5 H13.5 M2.5 11.5 H13.5"/></g></svg>
    <p class="contact" style="left:79px;top:241px">www.fernwellspinestudio.com</p>

    <div class="abs center follow">FOLLOW US</div>
    <div class="social-dot" style="left:113px"></div>
    <div class="social-dot" style="left:146px"></div>
    <div class="abs center handle">@fernwellspinestudio</div>
    <div class="page-no" style="left:285px;top:361px">04</div>
  </div>
</section>

</body>
</html>
```